Web site for a company that sells Pinball machines

We need a website that is an online shopping experience for a Store that sells pinball machines and accessories. The name of the store is called "Gadget Arcade." The store it self has a showroom, but we would also like to have an Internet e-commerce presence. We pinball machines made by Vexler pinball. You can visit their website and see their current list of machines as well as their website for the machines that we are going to carry in our store. Their website is Vexlerpinball.com. I am able to use their machine photos as well as their machine brochure PDF files. I am also able to use their logo on my website two list it as a Vexler Authorized Dealer.
This website design needs to be funky, fun, very technologically oriented and modern. The people buying machines our spending anywhere between $5000 and $15,000 on one machine. These Are high-end buyers who are also usually fairly tech savvy or at least enjoy technology and graphics.
Attachments: I have attached photographs of some of my own machines which may be used in the website. I've also attached some downloaded files from Vexler pinball.com as well as some of their PDF files for brochures. I will carry all of their current models they have listed under games. Not the archived games. I have included one of their machines called Thunderwolf Limited edition in my photograph attachments. The rest of the photos are just random pictures that I have taken myself and maybe used to build the site. Lastly I have attached my logo which I am not super crazy about so I will also be posting a contest to redesign this logo. Tons more of my own pinball photos are available.
I would like for people to be able to purchase machines and accessories from the website, but also inform them to our actual showroom.
Updates
Project Deadline Extended Reason: Hello. We have extended five days due to some complications during the construction of our actual building. We were unable to participate in this web design during this time and so unfortunately were not able give feedback appropriately. We are back on track and will provide feedback to the designers who have designed up until this point. We will still be interested in seeing new submissions, however; this extension will give us a chance to provide feedback and coordinate the website appropriately. Thank you so much for your submissions and your patience!!!!Gadget Arcade Added Friday, April 21, 2017
Target Market(s)
Target market is 16 to 75. Techy individuals to enjoy gaming technology video animation and Vegas style twinkle
Industry/Entity Type
It Company
Coding
Coded - Design and coding required
Number of Pages Required
3 page
Font styles to use
Look and feel
Each slider illustrates characteristics of the customer's brand and the style your logo design should communicate.

```html
<!DOCTYPE html>
<html lang="en">
<head>
<meta charset="utf-8">
<title>Gadget Arcade — Vexler Pinball Machines</title>
<link rel="stylesheet" href="https://fonts.googleapis.com/css2?family=Lato:wght@400;700;900&display=swap">
<style>
:root{
  --red:#e0262b;
  --red-dark:#b3161b;
  --ink:#111317;
  --slate:#3a4656;
  --slate-dark:#27313d;
  --teal:#1f3b46;
  --paper:#ececec;
  --white:#ffffff;
  --muted:#b9c1cb;
  --text:#4a4a4a;
}
*{box-sizing:border-box;margin:0;padding:0}
html,body{width:1200px;height:2400px;overflow:hidden}
body{font-family:"Lato",Arial,sans-serif;background:var(--ink);color:var(--white);position:relative}
a{color:inherit;text-decoration:none}

/* top bar */
.topbar{position:absolute;top:0;left:0;width:1200px;height:44px;background:#0b0c0e;display:flex;align-items:center;justify-content:space-between;padding:0 60px;z-index:3}
.search{display:flex;height:26px}
.search input{width:200px;border:0;padding:0 10px;font:400 12px "Lato",sans-serif;color:#555}
.search button{width:30px;border:0;background:var(--red);display:flex;align-items:center;justify-content:center}
.util-nav{display:flex;gap:28px;font-weight:700;font-size:14px;letter-spacing:.5px}

/* hero */
.hero{position:absolute;top:44px;left:0;width:1200px;height:664px;background:radial-gradient(ellipse at 50% 55%,#6a5a3c 0%,#2b2a2c 40%,#0d0e10 80%)}
.main-nav{position:absolute;top:20px;left:0;width:100%;display:flex;justify-content:center;gap:34px;font-weight:700;font-size:17px;letter-spacing:1px;z-index:2}
.main-nav span{display:flex;align-items:center;gap:10px}
.main-nav span::after{content:"";width:6px;height:6px;background:var(--red);transform:rotate(45deg)}
.main-nav span:last-child::after{display:none}
.hero-brand{position:absolute;top:150px;left:50%;transform:translateX(-50%);display:flex;align-items:center;gap:14px;font-weight:900;font-size:44px;letter-spacing:1px;z-index:2}
.hero-brand i{width:40px;height:40px;border-radius:50%;background:var(--red);display:block}

/* games band */
.games{position:absolute;top:708px;left:0;width:1200px;height:180px;background:linear-gradient(180deg,var(--slate),var(--slate-dark))}
.games h2{position:absolute;top:28px;left:60px;font-weight:900;font-size:30px}
.games p{position:absolute;top:74px;left:60px;width:780px;font-size:15px;line-height:1.5;color:#dfe4ea}
.buy-now{position:absolute;top:40px;right:110px;width:190px;height:70px;border-radius:35px;background:linear-gradient(#f5f5f5,#bfc3c7);color:#333;font-weight:900;font-size:18px;display:flex;align-items:center;justify-content:center;border:4px solid #8e959d}
.games svg{position:absolute;bottom:-1px;left:0}

/* welcome */
.welcome{position:absolute;top:888px;left:0;width:1200px;height:312px;background:var(--paper);color:var(--text)}
.welcome .seal{position:absolute;top:24px;left:116px;width:66px;height:66px;border-radius:50%;background:#9aa2ab}
.ribbon{position:absolute;top:74px;left:60px;width:560px;height:120px}
.ribbon .small{position:absolute;top:20px;left:90px;font-weight:900;font-size:20px;color:var(--white)}
.ribbon .big{position:absolute;top:52px;left:40px;font-weight:900;font-size:42px;color:var(--ink);letter-spacing:.5px}
.about-btn{position:absolute;top:208px;left:484px;width:130px;height:42px;border-radius:21px;background:var(--ink);color:var(--white);font-weight:700;font-size:14px;display:flex;align-items:center;justify-content:center;gap:8px}
.welcome .balls{position:absolute;left:60px;top:190px}
.welcome p{position:absolute;top:60px;left:680px;width:460px;font-size:15px;line-height:1.55;color:#666}

/* videos */
.videos{position:absolute;top:1200px;left:0;width:1200px;height:520px;background:linear-gradient(180deg,#121316,#1c1d21)}
.videos h2{text-align:center;margin-top:38px;font-weight:900;font-size:46px;letter-spacing:1px}
.videos .rule{width:260px;height:3px;background:var(--red);margin:6px auto 0}
.videos h3{text-align:center;font-weight:700;font-size:22px;margin-top:14px}
.videos .sub{text-align:center;font-size:15px;color:var(--red);margin-top:4px}
.video-row{position:absolute;top:200px;left:76px;display:flex;gap:64px}
.video{position:relative;width:488px;height:268px;border:3px solid #2d2f34}
.v1{background:linear-gradient(135deg,#3a2f5a,#7a3d4a 50%,#2a4a5a)}
.v2{background:linear-gradient(135deg,#3c3e44,#6c6a66 50%,#2f3034)}
.play{position:absolute;top:50%;left:50%;transform:translate(-50%,-50%)}

/* testimonial */
.clients{position:absolute;top:1720px;left:0;width:1200px;height:380px;background:var(--paper);color:var(--text)}
.clients .heading{position:absolute;top:28px;left:340px;width:520px;height:90px}
.clients .heading span{position:absolute;top:20px;left:0;width:100%;text-align:center;font-weight:900;font-size:38px;color:var(--ink)}
.quote-card{position:absolute;top:126px;left:176px;width:848px;height:176px;background:var(--white);box-shadow:0 6px 18px rgba(0,0,0,.18);border-bottom:6px solid var(--red)}
.quote-card .mark{position:absolute;top:14px;left:28px;font-weight:900;font-size:90px;color:#ddd;line-height:1}
.quote-card p{position:absolute;top:40px;left:140px;width:570px;text-align:center;font-size:16px;line-height:1.6;color:#666}
.quote-card .name{position:absolute;top:118px;left:0;width:100%;text-align:center;font-size:15px;color:var(--red);font-weight:700}
.dots{position:absolute;top:328px;left:0;width:100%;display:flex;justify-content:center;gap:10px}
.dots i{width:10px;height:10px;border-radius:50%;background:#333;display:block}
.dots i:first-child{background:var(--red)}

/* footer */
.footer{position:absolute;top:2100px;left:0;width:1200px;height:300px;background:linear-gradient(180deg,var(--teal),#122730);text-align:center}
.footer svg.edge{position:absolute;top:0;left:0}
.footer-brand{position:absolute;top:84px;left:0;width:100%;display:flex;justify-content:center;align-items:center;gap:10px;font-weight:900;font-size:24px}
.footer-brand i{width:24px;height:24px;border-radius:50%;background:var(--red);display:block}
.footer-nav{position:absolute;top:144px;left:0;width:100%;display:flex;justify-content:center;gap:10px;font-size:15px}
.footer-nav b{font-weight:400;color:var(--muted)}
.social{position:absolute;top:186px;left:0;width:100%;display:flex;justify-content:center;gap:14px}
.social i{width:34px;height:34px;border-radius:50%;display:block;background:var(--red)}
.social i+i{background:#56707c}
.copy{position:absolute;top:244px;left:0;width:100%;font-size:14px;color:var(--muted)}
</style>
</head>
<body>

<header class="topbar">
  <form class="search">
    <input type="text" value="Search Here..." aria-label="Search">
    <button type="button" aria-label="Search">
      <svg width="14" height="14" viewBox="0 0 14 14"><circle cx="6" cy="6" r="4.2" fill="none" stroke="#fff" stroke-width="1.8"/><path d="M9 9l4 4" stroke="#fff" stroke-width="2"/></svg>
    </button>
  </form>
  <nav class="util-nav"><a>HOME</a><a>STORY</a><a>VIDEOS</a><a>NEWS</a><a>BUY</a></nav>
</header>

<section class="hero" role="img" aria-label="Close-up photograph of a lit pinball playfield with flippers and a glowing ball">
  <nav class="main-nav"><span>ABOUT</span><span>GAMES</span><span>COMMUNITY</span><span>SUPPORT</span><span>BUY</span></nav>
  <div class="hero-brand"><i></i>Gadget Arcade</div>
</section>

<section class="games">
  <h2>GAMES</h2>
  <p>Lorem Ipsum is simply dummy text of the printing and typesetting industry. Lorem Ipsum has been the most industry's standard dummy text ever since the 1500s.</p>
  <a class="buy-now">BUY NOW</a>
  <svg width="1200" height="60" viewBox="0 0 1200 60"><polygon points="0,60 1200,60 1200,10 760,60 330,0" fill="#ececec"/><polygon points="330,0 760,60 560,60" fill="#e0262b"/><polygon points="1200,10 1200,60 1080,60" fill="#e0262b"/></svg>
</section>

<section class="welcome">
  <div class="seal"></div>
  <div class="ribbon">
    <svg width="560" height="120" viewBox="0 0 560 120"><polygon points="0,10 560,0 520,120 20,110" fill="#e0262b"/><polygon points="70,12 300,10 260,44 90,44" fill="#b3161b"/></svg>
    <span class="small">Welcome To</span>
    <span class="big">GADGET ARCADE</span>
  </div>
  <svg class="balls" width="300" height="100" viewBox="0 0 300 100"><circle cx="20" cy="20" r="12" fill="#8a939c"/><circle cx="90" cy="70" r="14" fill="#8a939c"/><circle cx="190" cy="40" r="10" fill="#8a939c"/><circle cx="260" cy="80" r="12" fill="#8a939c"/></svg>
  <a class="about-btn">ABOUT US <span>&#8250;</span></a>
  <p>Lorem Ipsum is simply dummy text of the printing and typesetting industry. Lorem Ipsum has been the industry's standard dummy text ever since the 1500s, when an unknown printer took a galley of type and scrambled it to make a type specimen book. It has survived not only five centuries, but also the leap into electronic typesetting, remaining essentially unchanged. It was popularised in the 1960s with the release of...</p>
</section>

<section class="videos">
  <h2>LATEST VIDEOS</h2>
  <div class="rule"></div>
  <h3>Your All - Access Pass to Everything Vexler</h3>
  <p class="sub">Use our Community Page for more Game, Event and Instructional Videos</p>
  <div class="video-row">
    <div class="video v1" role="img" aria-label="Video still of colourful pinball machines in a showroom">
      <svg class="play" width="60" height="42" viewBox="0 0 60 42"><rect width="60" height="42" rx="10" fill="#e0262b"/><polygon points="24,12 40,21 24,30" fill="#fff"/></svg>
    </div>
    <div class="video v2" role="img" aria-label="Video still of a row of pinball cabinets">
      <svg class="play" width="60" height="42" viewBox="0 0 60 42"><rect width="60" height="42" rx="10" fill="#e0262b"/><polygon points="24,12 40,21 24,30" fill="#fff"/></svg>
    </div>
  </div>
</section>

<section class="clients">
  <div class="heading">
    <svg width="520" height="90" viewBox="0 0 520 90"><polygon points="0,0 520,20 500,80 30,70" fill="#e0262b"/><polygon points="40,12 480,26 470,64 50,58" fill="#ececec"/></svg>
    <span>WHAT OUR CLIENT SAY</span>
  </div>
  <div class="quote-card">
    <span class="mark">&ldquo;</span>
    <p>Lorem Ipsum is simply dummy text of the printing and typesetting industry. Lorem Ipsum has been the industry's standard dummy text ever since the 1500s.</p>
    <span class="name">&mdash; Client Name</span>
  </div>
  <div class="dots"><i></i><i></i><i></i></div>
</section>

<footer class="footer">
  <svg class="edge" width="1200" height="60" viewBox="0 0 1200 60"><polygon points="0,0 1200,0 1200,20 900,0 620,50 0,10" fill="#ececec"/><polygon points="0,10 360,30 0,60" fill="#e0262b"/><polygon points="900,0 1200,20 1200,50" fill="#e0262b"/></svg>
  <div class="footer-brand"><i></i>Gadget Arcade</div>
  <nav class="footer-nav"><a>About</a><b>|</b><a>Games</a><b>|</b><a>Community</a><b>|</b><a>Support</a><b>|</b><a>Buy</a></nav>
  <div class="social"><i></i><i></i><i></i><i></i></div>
  <p class="copy">&copy; GADGET ARCADE - 2017, All Rights Reserved.</p>
</footer>

</body>
</html>
```